Core Value Graphic for a Service Disabled and Minority Certified contractor

My company, Keystone Aid Partners, is a US Federal Contractor that hires veterans and service disabled veterans. Our website is www.keystoneaid7.example. We work hard to maintain a 50:50 split between veterans and non-veterans on our team. Our tagline is "To Find a Better Way." We are continually looking to integrate technology and efficiency into all that we do.

I want a way to express our company core values visually so that our employees and customers alike can read them and get a sense of who we are, what drives us to succeed, and what makes up our team DNA.

I need an artist like you to help me represent our core values visually. In a manner that I can print it out on an 8"X11" sheet of paper or a large 48" X 48" poster, without losing the visual clarity or that it pixelates out of focus. I am looking for a color scheme that is patriotic with Red, White, and Blues and similar hues. I would also like to incorporate my logo and tagline into the design in some manner.

I have attached several examples of a Core Value Grids from other companies. I am hopeful it will inspire you, and a get your brain juices flowing to provide me with a knockout Core Value Grid that will rock only you can provide! I also include a copy of my company Core Values and a copy of our Logo.

Looking forward to seeing your creations. Thanks.

Target Market(s)

Employees, any potential strategic alliance partners, and customers.

Industry/Entity Type

Contractor

Requirements
Must have
• Patriotic feel and have my logo someplace on the document.

```html
<!DOCTYPE html>
<html lang="en">
<head>
<meta charset="utf-8">
<title>Keystone Aid Partners – Our Core Values</title>
<link href="https://fonts.googleapis.com/css2?family=Arimo:wght@700&family=Roboto+Condensed:wght@700&display=swap" rel="stylesheet">
<style>
  :root{
    --page:#e4e4e4;
    --ink:#111111;
    --navy:#1b1f45;
    --navy-deep:#14173a;
    --red:#a3161b;
    --red-bright:#c01f25;
    --silver:#d9dae6;
    --steel:#8a8cb0;
    --white:#ffffff;
  }
  *{box-sizing:border-box;margin:0;padding:0}
  html,body{width:1200px;height:1000px;overflow:hidden;background:var(--page)}
  .poster{
    position:absolute;left:153px;top:10px;width:744px;height:816px;overflow:hidden;
    transform:scale(1.2);transform-origin:0 0;background:var(--navy);
    font-family:"Roboto Condensed","Arial Narrow",sans-serif;font-weight:700;color:var(--ink);
  }
  .header{
    position:absolute;left:0;top:0;width:744px;height:104px;
    background:linear-gradient(90deg,#111 0%,#1a1a1a 35%,#4b4c6a 60%,var(--steel) 78%,var(--silver) 100%);
  }
  .brand{
    position:absolute;left:28px;top:42px;display:flex;align-items:center;gap:8px;
    color:var(--white);font-size:15px;text-transform:uppercase;letter-spacing:.5px;
  }
  .brand-mark{width:14px;height:14px;background:var(--red-bright)}
  .title{
    position:absolute;font-family:"Arimo",Arial,sans-serif;font-weight:700;color:var(--white);
    white-space:nowrap;line-height:1;transform:scaleX(.73);transform-origin:0 0;
  }
  .title .small{font-size:46px}
  .title .big{font-size:64px}
  .header .title{left:282px;top:20px;text-shadow:0 0 2px #555}
  .field{
    position:absolute;left:0;top:104px;width:744px;height:633px;
    background:
      radial-gradient(ellipse 60% 45% at 20% 70%,rgba(70,80,150,.55),transparent 70%),
      radial-gradient(ellipse 55% 60% at 85% 30%,rgba(163,22,27,.75),transparent 70%),
      radial-gradient(ellipse 50% 40% at 70% 85%,rgba(163,22,27,.5),transparent 70%),
      linear-gradient(135deg,var(--navy-deep),var(--navy) 50%,#2a2f63);
  }
  .footer{
    position:absolute;left:0;top:737px;width:744px;height:79px;
    background:linear-gradient(90deg,var(--silver) 0%,var(--steel) 25%,#3a3b55 50%,#161616 75%,#111 100%);
    border-top:2px solid var(--white);
  }
  .footer .title{left:14px;top:8px;text-shadow:0 0 2px #333}
  .links{position:absolute;left:0;top:0;width:744px;height:816px}
  .value{
    position:absolute;background:var(--white);text-align:center;
    text-transform:uppercase;font-size:8.4px;line-height:1.42;padding:6px 6px 5px;
    display:flex;flex-direction:column;justify-content:space-evenly;
  }
  .value h3{color:var(--red);font-size:10px;line-height:1.2;margin:1px 0}
  .tag{
    position:absolute;background:linear-gradient(90deg,var(--red),var(--red-bright));
    color:var(--white);font-size:9.6px;line-height:1.1;text-align:center;
    padding:3px 5px;box-shadow:2px 2px 0 rgba(255,255,255,.6);
  }
  .tagline{
    position:absolute;left:321px;top:380px;width:100px;height:85px;
    background:var(--navy-deep);border:1.5px solid var(--white);color:var(--white);
    font-size:18px;line-height:1.15;text-align:center;text-transform:uppercase;
    display:flex;align-items:center;justify-content:center;
  }
</style>
</head>
<body>
<div class="poster">
  <header class="header">
    <div class="brand"><span class="brand-mark"></span>Keystone Aid Partners</div>
    <div class="title"><span class="small">OUR </span><span class="big">CORE VALUES</span></div>
  </header>

  <div class="field" role="img" aria-label="Abstract red and blue flag swoosh backdrop"></div>

  <svg class="links" viewBox="0 0 744 816" aria-hidden="true">
    <defs>
      <polygon id="star" points="0,-14 3.5,-4.9 13.3,-4.3 5.7,1.9 8.2,11.3 0,6 -8.2,11.3 -5.7,1.9 -13.3,-4.3 -3.5,-4.9" fill="#fff" stroke="#1b1f45" stroke-width="1.6"/>
    </defs>
    <g fill="none" stroke="#fff" stroke-width="1.2">
      <polyline points="342,380 342,222 342,200"/>
      <polyline points="396,380 396,314 396,290 424,290"/>
      <polyline points="421,408 466,408 475,408 475,430 503,430"/>
      <polyline points="321,430 269,430 255,430 255,455 244,455"/>
      <polyline points="400,465 400,480 448,480 448,510"/>
    </g>
    <use href="#star" x="342" y="222"/>
    <use href="#star" x="396" y="314"/>
    <use href="#star" x="466" y="408"/>
    <use href="#star" x="269" y="435"/>
    <use href="#star" x="448" y="480"/>
  </svg>

  <div class="tagline">To Find<br>a Better<br>Way</div>

  <section class="value" style="left:87px;top:148px;width:217px;height:221px">
    <h3>What it means</h3>
    <p>Safety takes precedence over every phase of the day’s operation.</p>
    <h3>How to express it</h3>
    <p>Anyone can call a stop to the work in progress if an unsafe act is occurring. In fact, it is each team member’s duty to do so, rectify the unsafe issue, then proceed. Never hesitate; everyone comes back. Finally, each after action review begins with discussing safety issues. We always let everyone on the team know of an unsafe situation, so it can be avoided in the future.</p>
    <h3>Result</h3>
    <p>All team members go home to their loved ones each day to pursue their individual happiness</p>
  </section>
  <div class="tag" style="left:90px;top:120px;width:108px">Everyone comes back to the Green Zone.</div>

  <section class="value" style="left:424px;top:149px;width:206px;height:220px">
    <h3>What it means</h3>
    <p>We weave innovation into the fabric that makes up our company.</p>
    <h3>How to express it</h3>
    <p>We’re early adopters of technology. We quickly evaluate new technologies or processes that could separate us from our competition. Then we implement and evaluate these new technologies. We dump it quickly if we see it is not helping us achieve “commander’s intent.” We have the guts to be first. We iterate continuously and attack, attack, attack.</p>
    <h3>Result</h3>
    <p>We will be ahead of our competition. It’s one mechanism that helps us scale. Prosperity favors the bold!</p>
  </section>
  <div class="tag" style="left:428px;top:121px;width:110px">Boldly go.<br>Seek. Find.</div>

  <section class="value" style="left:20px;top:405px;width:224px;height:245px">
    <h3>What it means</h3>
    <p>We always help your team members be successful. Commitment to each other and to our own personal integrity is the fuel that empowers us.</p>
    <h3>How to express it</h3>
    <p>If a wingman is having challenges accomplishing their individual priorities or completing their assigned mission, volunteer to help them to do so. This goes for subs/suppliers as well. We help those who help us succeed! Always look to establish the best win-win relationship possible, and do what you can to support them if they get into a bind.</p>
    <h3>Result</h3>
    <p>Be there for them and they will be there for us.</p>
  </section>
  <div class="tag" style="left:28px;top:380px;width:120px">Never leave your wingman.</div>

  <section class="value" style="left:503px;top:404px;width:225px;height:183px">
    <h3>What it means</h3>
    <p>No leader will put themselves ahead of their subordinates.</p>
    <h3>How to express it</h3>
    <p>We lead by example. Demonstrate the moral courage and discipline to do the right thing at the highest level of quality.</p>
    <h3>Result</h3>
    <p>Every new team member will quickly realize their leaders genuinely care for their welfare and success. This is the best way to drive esprit de corps and achieve excellence.</p>
  </section>
  <div class="tag" style="left:506px;top:380px;width:116px">Troops (Team Members) eat first.</div>

  <section class="value" style="left:262px;top:510px;width:228px;height:222px">
    <h3>What it means</h3>
    <p>If you’re not making mistakes, you’re not taking enough chances or getting out of your comfort zone.</p>
    <h3>How to express it</h3>
    <p>Use your best judgment when trying something new. But, don’t let your pride keep you from saying, “I was wrong” when your idea doesn’t work. We trust you will know when it’s time to dump the idea, or stop doing something that doesn’t work.</p>
    <h3>Result</h3>
    <p>No one will ever be penalized for making a mistake. Don’t be afraid to try something you believe will work. That’s how we grow ourselves and our team members.</p>
  </section>
  <div class="tag" style="left:292px;top:483px;width:88px">Fail quickly and learn</div>

  <footer class="footer">
    <div class="title"><span class="small">OUR </span><span class="big">CORE VALUES</span></div>
  </footer>
</div>
</body>
</html>
```